Harbor Crestline (Business Card Design)

Need business cards designed. Something modern, chic, and sleek. Mabye the back of the card should be the navy blue that is in the logo and then just the logo on the back.

Target Market(s)

Those in the hotel, office, and renovation industry

Contact Information for Business Card

1. Logo 2. Dorian Fenwick 3. CEO/Founder 4. Phone: (833) HarbCre / (833) 427-2731 5. Email: dorian@theharborcrestline.com 6. Website: www.theharborcrestline.com

Font styles to use
Other font styles liked:
• Look at the logo font and base the font for everything else off of that.

Colors
0054AA
0677BA
7BADD7
CADEEF
E8F1F8

Requirements
Must have
• Colors that are associated in the logo
Nice to have
• Sleek modern clean and chic design.

```html
<!DOCTYPE html>
<html lang="en">
<head>
<meta charset="utf-8">
<title>Harbor Crestline – Business Card</title>
<link rel="stylesheet" href="https://fonts.googleapis.com/css2?family=Montserrat:wght@500&family=Open+Sans:wght@400;700&display=swap">
<style>
  :root {
    --stage: #2b2b2e;
    --navy: #0c1849;
    --navy-deep: #08113a;
    --navy-emboss: #1d2a68;
    --lavender: #8b86c9;
    --gold: #c9a23a;
    --white: #ffffff;
  }
  * { margin: 0; padding: 0; box-sizing: border-box; }
  html, body {
    width: 1200px; height: 780px; overflow: hidden;
    background: var(--stage);
  }
  .sheet {
    width: 1200px; height: 780px;
    display: flex; align-items: center; justify-content: center; gap: 60px;
  }
  .card {
    position: relative;
    width: 520px; height: 297px;
    background: var(--navy);
    border-radius: 3px;
    box-shadow: 0 14px 30px rgba(0,0,0,.45);
    overflow: hidden;
  }
  /* Front */
  .brand-decoration {
    position: absolute; left: 38px; top: 48px;
    width: 200px; height: 200px;
    border-radius: 4px;
    background: linear-gradient(100deg, var(--navy-deep) 0%, var(--navy-emboss) 55%, var(--lavender) 100%);
    opacity: .85;
  }
  .front-info {
    position: absolute; right: 36px; top: 30px;
    text-align: right; color: var(--white);
    font-family: "Open Sans", sans-serif;
  }
  .lockup {
    display: flex; align-items: center; justify-content: flex-end; gap: 10px;
    margin-bottom: 22px;
  }
  .lockup-mark {
    width: 26px; height: 26px; border: 3px solid var(--white);
  }
  .lockup-name {
    font-family: "Montserrat", sans-serif; font-weight: 500;
    font-size: 20px; letter-spacing: 2px; text-transform: uppercase;
    color: var(--white);
  }
  .person-name {
    font-weight: 700; font-size: 27px; line-height: 1.05;
    color: var(--gold);
  }
  .person-title { font-size: 13px; margin-top: 3px; margin-bottom: 14px; }
  .address { font-size: 11.5px; line-height: 1.45; margin-bottom: 8px; }
  .contact-line {
    display: flex; align-items: center; justify-content: flex-end; gap: 7px;
    font-size: 11.5px; line-height: 1.6;
  }
  .contact-icon { width: 11px; height: 11px; fill: var(--gold); flex: none; }
  .gold-tab {
    position: absolute; right: 0; top: 104px;
    width: 14px; height: 44px; background: var(--gold);
  }
  /* Back */
  .back-lockup {
    position: absolute; inset: 0;
    display: flex; align-items: center; justify-content: center; gap: 14px;
  }
  .back-lockup .lockup-mark { border-color: var(--navy-emboss); width: 36px; height: 36px; border-width: 4px; }
  .back-lockup .lockup-name { color: var(--navy-emboss); font-size: 28px; letter-spacing: 3px; }
</style>
</head>
<body>
<main class="sheet">
  <section class="card card-front" aria-label="Business card front">
    <div class="brand-decoration" role="img" aria-label="Large faded brand square decoration"></div>
    <div class="gold-tab"></div>
    <div class="front-info">
      <div class="lockup">
        <span class="lockup-mark"></span>
        <span class="lockup-name">Harbor Crestline</span>
      </div>
      <p class="person-name">Dorian Fenwick</p>
      <p class="person-title">CEO/Founder</p>
      <p class="address">4120 Meridian Pkwy<br>Suite 2200, Ellicott, MD 21043</p>
      <p class="contact-line">(833) HarbCre / (833) 427-2731
        <svg class="contact-icon" viewBox="0 0 24 24" aria-hidden="true"><path d="M6.6 10.8a15.1 15.1 0 0 0 6.6 6.6l2.2-2.2c.3-.3.7-.4 1-.2 1.1.4 2.3.6 3.6.6.6 0 1 .4 1 1V20c0 .6-.4 1-1 1A17 17 0 0 1 3 4c0-.6.4-1 1-1h3.5c.6 0 1 .4 1 1 0 1.3.2 2.5.6 3.6.1.3 0 .7-.2 1z"/></svg>
      </p>
      <p class="contact-line">www.theharborcrestline.com
        <svg class="contact-icon" viewBox="0 0 24 24" aria-hidden="true"><path d="M12 2a10 10 0 1 0 0 20 10 10 0 0 0 0-20zm6.9 6h-2.9a15.6 15.6 0 0 0-1.4-3.6A8 8 0 0 1 18.9 8zM12 4c.8 1.2 1.5 2.5 1.9 4h-3.8c.4-1.4 1.1-2.8 1.9-4zM4.3 14a8.2 8.2 0 0 1 0-4h3.4a16.5 16.5 0 0 0 0 4zm.8 2h2.9c.3 1.3.8 2.5 1.4 3.6A8 8 0 0 1 5.1 16zM8 8H5.1a8 8 0 0 1 4.3-3.6C8.8 5.5 8.3 6.7 8 8zm4 12c-.8-1.2-1.5-2.5-1.9-4h3.8c-.4 1.4-1.1 2.8-1.9 4zm2.3-6H9.7a14.7 14.7 0 0 1 0-4h4.6a14.7 14.7 0 0 1 0 4zm.3 5.6c.6-1.1 1.1-2.3 1.4-3.6h2.9a8 8 0 0 1-4.3 3.6zm1.7-5.6a16.5 16.5 0 0 0 0-4h3.4a8.2 8.2 0 0 1 0 4z"/></svg>
      </p>
      <p class="contact-line">dorian@theharborcrestline.com
        <svg class="contact-icon" viewBox="0 0 24 24" aria-hidden="true"><path d="M3 5h18c.6 0 1 .4 1 1v12c0 .6-.4 1-1 1H3c-.6 0-1-.4-1-1V6c0-.6.4-1 1-1zm9 7.2L4.3 7v10h15.4V7z"/></svg>
      </p>
    </div>
  </section>

  <section class="card card-back" aria-label="Business card back">
    <div class="back-lockup">
      <span class="lockup-mark"></span>
      <span class="lockup-name">Harbor Crestline</span>
    </div>
  </section>
</main>
</body>
</html>
```